Architectural, Engineering and Design Build

Tovandex4.com
Veteran Disabled Certified company is doing business in Architecture, Engineer and Design build - look simialr websites and come up with design follow following website
https://hollis-darnet.example/
https://www.venlorcogroup.example/
https://www.pembrisgc.example/contract-vehicles/service-disabled-veteran-owned-small-business-sdvosb/
https://www.corbelnetlink.example/about/sdvosb/

Target Market(s)

US - Defense and Federal Government

Industry/Entity Type

Colors
0054AA
0677BA
7BADD7
CADEEF
E8F1F8

Requirements
Must have
• Army, American patriotism , Buildings, construction, architecture, engineering
Nice to have
• I need to attract federal government agencies and Defense

```html
<!DOCTYPE html>
<html lang="en">
<head>
<meta charset="utf-8">
<title>Tovandex4 Architectural Engineering Construction</title>
<link rel="stylesheet" href="https://fonts.googleapis.com/css2?family=Exo+2:wght@600;700&family=Outfit:wght@400;500;600;700&display=swap">
<style>
:root{
  --navy:#15243a;
  --navy-deep:#0f1c2e;
  --blue:#0054AA;
  --blue-mid:#0677BA;
  --blue-soft:#7BADD7;
  --blue-pale:#CADEEF;
  --blue-mist:#E8F1F8;
  --red:#d41f26;
  --ink:#161616;
  --white:#ffffff;
}
*{margin:0;padding:0;box-sizing:border-box}
html,body{width:1200px;height:4626px;overflow:hidden;background:var(--white)}
body{font-family:"Outfit",sans-serif;color:var(--ink)}
.page{position:relative;width:1200px;height:4626px;overflow:hidden}
.abs{position:absolute}
.photo{position:absolute;display:block}
h1,h2,h3,h4{font-weight:600}
.btn{position:absolute;display:flex;align-items:center;justify-content:center;border-radius:22px;color:var(--white);font-size:14px;font-weight:500}
.arrow-bullet{display:inline-block;width:18px;height:18px;vertical-align:middle;margin-right:9px}

/* hero */
.hero{position:absolute;left:0;top:0;width:1200px;height:600px}
.hero-photo{left:0;top:0;width:1200px;height:600px;background:linear-gradient(180deg,#3f6b9a 0%,#7d9cbc 30%,#c9cfd5 55%,#a3a29d 78%,#8c8780 100%)}
.hero-shade{left:0;top:0;width:700px;height:600px;background:linear-gradient(90deg,rgba(18,40,72,.55),rgba(18,40,72,0))}
.brand{left:140px;top:44px;display:flex;align-items:center;gap:10px;color:var(--white);font-family:"Outfit",sans-serif;font-weight:700;font-size:28px}
.brand-dot{width:14px;height:14px;border-radius:50%;background:var(--white)}
.hero-mail{left:853px;top:22px;display:flex;gap:10px;align-items:center;color:var(--white);font-size:12px;line-height:15px}
.icon-ring{width:32px;height:32px;border-radius:50%;background:var(--white);display:flex;align-items:center;justify-content:center}
.menu-btn{left:1028px;top:24px;width:30px;height:30px;border-radius:50%;background:var(--white);display:flex;align-items:center;justify-content:center}
.hero-title{left:143px;top:212px;font-family:"Exo 2",sans-serif;font-weight:700;font-size:46px;line-height:54px;color:var(--white);letter-spacing:.5px}
.hero-btn{left:142px;top:395px;width:153px;height:38px;background:var(--red);font-size:13px}

/* services */
.section-title{font-size:31px;font-weight:600;letter-spacing:.3px;color:var(--ink)}
.services-title{left:141px;top:712px}
.services-lead{left:142px;top:766px;width:560px;font-size:14px;line-height:23px}
.services-photo{left:142px;top:857px;width:453px;height:363px;background:linear-gradient(180deg,#8fb1d3 0%,#b9cde0 45%,#8d8a82 75%,#5b6e7c 100%)}
.services-list{left:659px;top:898px}
.services-list h3{margin-top:100px;font-size:16px;font-weight:600}
.services-list ul{list-style:none;margin-top:14px}
.services-list li{font-size:13px;height:40px;display:flex;align-items:center}
.feature-card{top:1277px;width:293px;height:228px;border-radius:2px;overflow:hidden}
.feature-card .photo{left:0;top:0;width:100%;height:100%}
.feature-card p{position:absolute;left:21px;bottom:28px;right:20px;color:var(--white);font-size:12px;line-height:19px;font-weight:500}

/* why choose */
.why-bg{left:0;top:1600px;width:1200px;height:660px}
.why-title{left:0;top:1755px;width:1200px;text-align:center;color:var(--white);font-size:29px}
.why-lead{left:355px;top:1803px;width:490px;text-align:center;color:var(--white);font-size:12px;line-height:19px}
.why-item{top:1878px;width:270px;text-align:center;color:var(--white)}
.why-ring{width:102px;height:102px;border:2px solid var(--white);border-radius:50%;margin:0 auto;display:flex;align-items:center;justify-content:center}
.why-item h4{margin-top:27px;font-size:15px;font-weight:600}
.why-item p{margin-top:8px;font-size:11px;line-height:19px;padding:0 10px}

/* about */
.about-bg{left:0;top:2256px;width:1200px;height:1060px}
.about-title{left:0;top:2338px;width:1200px;text-align:center}
.about-heading{left:142px;top:2488px;font-size:24px;line-height:32px;font-weight:600}
.about-text{left:142px;top:2561px;width:400px;font-size:14px;line-height:24px}
.mission{left:141px;top:2678px;font-size:18px;font-weight:600}
.mission-items{left:141px;top:2723px;display:flex;gap:38px;font-size:12px;align-items:center}
.about-btn{left:142px;top:2775px;width:117px;height:45px;background:var(--blue);font-size:14px}
.about-frame{left:663px;top:2412px;width:417px;height:440px;background:var(--white);box-shadow:0 8px 28px rgba(20,40,70,.12)}
.about-photo{left:605px;top:2434px;width:453px;height:443px;background:linear-gradient(180deg,#2a6fc7 0%,#4b8ddb 45%,#a9c7ea 70%,#6e6a61 90%,#4e5a66 100%)}

/* team */
.team-title{left:0;top:2946px;width:1200px;text-align:center;font-size:24px}
.team-card{top:3024px;width:222px;text-align:center}
.team-photo{position:relative;width:222px;height:222px;border-radius:50%;background:linear-gradient(180deg,#c9c6c0 0%,#9b968c 55%,#4b4f56 100%)}
.team-card h4{margin-top:24px;font-size:12px;font-weight:600}
.team-card p{margin-top:4px;font-size:11px}
.nav-arrow{width:58px;height:58px;border-radius:50%;display:flex;align-items:center;justify-content:center}
.nav-arrow.prev{background:var(--blue-mist);border:1px solid var(--blue-pale)}
.nav-arrow.next{background:var(--blue-mid)}

/* testimonials */
.testi-title{left:0;top:3384px;width:1200px;text-align:center;font-size:30px}
.testi-card{top:3497px;width:445px;height:274px;border-radius:22px}
.testi-card.soft{left:142px;background:var(--blue-mist)}
.testi-card.plain{left:613px;background:var(--white);box-shadow:0 6px 22px rgba(20,40,70,.13)}
.quote-badge{position:absolute;top:-22px;width:56px;height:54px;border-radius:12px;background:var(--blue);display:flex;align-items:center;justify-content:center}
.testi-card .quote{position:absolute;left:28px;top:68px;width:395px;font-size:15px;line-height:28px}
.testi-avatar{position:absolute;left:26px;top:162px;width:80px;height:80px;border-radius:50%;background:linear-gradient(180deg,#d8c8b4,#8f7c6a)}
.testi-card h4{position:absolute;left:126px;top:178px;font-size:22px;font-weight:600}
.testi-card .role{position:absolute;left:126px;top:210px;font-size:13px}

/* cta */
.cta-bg{left:0;top:3870px;width:1200px;height:400px;background:linear-gradient(180deg,#e3ecf5 0%,#d3e1ee 100%)}
.cta-title{left:0;top:3940px;width:1200px;text-align:center;font-size:25px}
.cta-sub{left:0;top:3990px;width:1200px;text-align:center;font-size:13px;font-weight:500}
.cta-btn{left:510px;top:4028px;width:180px;height:42px;background:var(--blue-mid);font-size:14px}

/* footer */
.footer-bg{left:0;top:4170px;width:1200px;height:456px}
.footer-col h3{color:var(--white);font-size:24px;font-weight:600}
.quick-links{left:154px;top:4286px}
.quick-links ul{list-style:none;margin-top:18px}
.quick-links li{color:var(--white);font-size:14px;font-weight:500;height:38.5px}
.contact-info{left:436px;top:4286px;width:300px}
.contact-row{display:flex;gap:14px;color:var(--white);font-size:14px;font-weight:500;line-height:23px;margin-top:16px}
.contact-row svg{flex:none;margin-top:3px}
.footer-brand{left:780px;top:4350px;width:296px;text-align:center;color:var(--white)}
.footer-brand .name{font-size:32px;font-weight:700;display:flex;align-items:center;justify-content:center;gap:10px}
.footer-brand .tag{margin-top:30px;font-size:13px;font-weight:500}
.socials{display:flex;gap:16px;justify-content:center;margin-top:20px}
.socials span{width:33px;height:33px;border:1.5px solid var(--white);border-radius:50%}
.copyright{left:0;top:4576px;width:1200px;height:50px;background:var(--blue);color:var(--white);font-size:12px;display:flex;align-items:center;justify-content:center}
</style>
</head>
<body>
<div class="page">

  <!-- hero -->
  <header class="hero">
    <div class="photo hero-photo" role="img" aria-label="Capitol building with white columns and dome under a blue sky with clouds"></div>
    <div class="photo hero-shade"></div>
    <div class="abs brand"><span class="brand-dot"></span>Tovandex4</div>
    <div class="abs hero-mail">
      <span class="icon-ring"><svg width="14" height="11" viewBox="0 0 14 11"><rect x="0.5" y="0.5" width="13" height="10" rx="1" fill="var(--red)"/><path d="M1 1l6 5 6-5" stroke="#fff" stroke-width="1.2" fill="none"/></svg></span>
      <span>Email<br>info@tovandex4.com</span>
    </div>
    <div class="abs menu-btn"><svg width="14" height="10" viewBox="0 0 14 10"><path d="M0 1h14M0 5h14M0 9h9" stroke="var(--red)" stroke-width="1.6"/></svg></div>
    <h1 class="abs hero-title">BUILDING FOR<br>THE FUTURE<br>OF DEFENSE</h1>
    <div class="btn hero-btn">Contact Us Today!</div>
  </header>

  <!-- services -->
  <h2 class="abs section-title services-title">OUR SERVICES</h2>
  <p class="abs services-lead">Lorem ipsum dolor sit amet, consectetur adipiscing elit, sed do eiusmod tempor aliqua Quis ipsum.</p>
  <div class="photo services-photo" role="img" aria-label="City skyline with tower crane and high-rise under construction"></div>
  <div class="abs services-list">
    <svg class="abs" style="left:0;top:0" width="64" height="76" viewBox="0 0 64 76" fill="none" stroke="#111" stroke-width="2.4"><rect x="2" y="2" width="48" height="70" rx="3"/><path d="M10 24V16M18 24V10M26 24V14M34 24V8M42 24V18"/><rect x="9" y="32" width="8" height="8"/><path d="M22 36h20"/><rect x="9" y="48" width="8" height="8"/><path d="M22 52h12"/><circle cx="50" cy="56" r="10"/><circle cx="50" cy="56" r="4"/></svg>
    <h3>Clear and concise descriptions</h3>
    <ul>
      <li><svg class="arrow-bullet" viewBox="0 0 18 18"><path d="M2 2l14 7-14 7 4-7z" fill="none" stroke="#111" stroke-width="1.6" stroke-linejoin="round"/></svg>Core architectural</li>
      <li><svg class="arrow-bullet" viewBox="0 0 18 18"><path d="M2 2l14 7-14 7 4-7z" fill="none" stroke="#111" stroke-width="1.6" stroke-linejoin="round"/></svg>Engineering</li>
      <li><svg class="arrow-bullet" viewBox="0 0 18 18"><path d="M2 2l14 7-14 7 4-7z" fill="none" stroke="#111" stroke-width="1.6" stroke-linejoin="round"/></svg>Design-build services</li>
      <li><svg class="arrow-bullet" viewBox="0 0 18 18"><path d="M2 2l14 7-14 7 4-7z" fill="none" stroke="#111" stroke-width="1.6" stroke-linejoin="round"/></svg>Defense and government sector</li>
    </ul>
  </div>

  <div class="abs feature-card" style="left:142px">
    <div class="photo" role="img" aria-label="Engineer in hard hat beside a tall building under construction" style="background:linear-gradient(180deg,#b5bcc4 0%,#8a8f95 55%,#2c3038 100%)"></div>
    <p>Lorem ipsum dolor sit amet, consectetur adipiscing elit, sed do.</p>
  </div>
  <div class="abs feature-card" style="left:454px">
    <div class="photo" role="img" aria-label="Grand government hall interior with a flag" style="background:linear-gradient(180deg,#a48a63 0%,#6f5a3f 55%,#241d16 100%)"></div>
    <p>Lorem ipsum dolor sit amet, consectetur adipiscing elit, sed do.</p>
  </div>
  <div class="abs feature-card" style="left:765px">
    <div class="photo" role="img" aria-label="Construction workers in hard hats on a building site" style="background:linear-gradient(180deg,#9aa3ab 0%,#767c80 55%,#2b2f34 100%)"></div>
    <p>Lorem ipsum dolor sit amet, consectetur adipiscing elit, sed do.</p>
  </div>

  <!-- why choose -->
  <svg class="abs why-bg" viewBox="0 0 1200 660" preserveAspectRatio="none">
    <polygon points="0,80 359,0 1200,108 1200,124 359,20 0,106" fill="var(--blue-mid)"/>
    <polygon points="0,97 359,7 1200,124 1200,546 840,656 0,537" fill="#1a2a42" role="img" aria-label="Historic arched hall interior with American flags, darkened"/>
    <polygon points="0,537 840,656 1200,546 1200,565 840,660 0,560" fill="var(--blue-mid)"/>
  </svg>
  <h2 class="abs why-title">WHY CHOOSE US?</h2>
  <p class="abs why-lead">Lorem ipsum dolor sit amet, consectetur adipiscing elit, sed do eiusmod tempor aliqua Quis ipsum.</p>
  <div class="abs why-item" style="left:140px">
    <div class="why-ring"><svg width="56" height="52" viewBox="0 0 56 52" fill="none" stroke="#fff" stroke-width="2"><circle cx="28" cy="10" r="6"/><circle cx="12" cy="16" r="5"/><circle cx="44" cy="16" r="5"/><path d="M4 44c2-10 8-14 16-14l8 8 8-8c8 0 14 4 16 14M20 30l8 10 8-10"/></svg></div>
    <h4>Veteran-Owned Business</h4>
    <p>Lorem Ipsum is simply dummy text of the printing and typesetting industry. Lorem Ipsum has been the industry's ever</p>
  </div>
  <div class="abs why-item" style="left:460px">
    <div class="why-ring"><svg width="56" height="52" viewBox="0 0 56 52" fill="none" stroke="#fff" stroke-width="2"><circle cx="28" cy="10" r="6"/><path d="M18 30c2-7 6-9 10-9s8 2 10 9"/><path d="M10 34l3 6 6 1-4 4 1 6-6-3-6 3 1-6-4-4 6-1zM28 34l3 6 6 1-4 4 1 6-6-3-6 3 1-6-4-4 6-1zM46 34l3 6 6 1-4 4 1 6-6-3-6 3 1-6-4-4 6-1z"/></svg></div>
    <h4>Experience and Expertise</h4>
    <p>Lorem Ipsum is simply dummy text of the printing and typesetting industry. Lorem Ipsum has been the industry's ever</p>
  </div>
  <div class="abs why-item" style="left:781px">
    <div class="why-ring"><svg width="56" height="52" viewBox="0 0 56 52" fill="none" stroke="#fff" stroke-width="2"><circle cx="30" cy="16" r="12"/><path d="M24 16l4 4 8-8"/><path d="M4 40h10l10 4h14l12-8-4-3-12 5h-10"/><path d="M4 36v12"/></svg></div>
    <h4>Commitment to Quality</h4>
    <p>Lorem Ipsum is simply dummy text of the printing and typesetting industry. Lorem Ipsum has been the industry's ever</p>
  </div>

  <!-- about -->
  <svg class="abs about-bg" viewBox="0 0 1200 1060" preserveAspectRatio="none">
    <rect width="1200" height="1060" fill="#f7fafd"/>
    <polygon points="250,0 700,0 1200,500 1200,900 600,900 250,500" fill="var(--blue-mist)" opacity=".7"/>
    <polygon points="0,150 360,520 0,900" fill="var(--blue-mist)" opacity=".8"/>
  </svg>
  <h2 class="abs section-title about-title">ABOUT US</h2>
  <h3 class="abs about-heading">TOVANDEX4 ARCHITECTURAL<br>ENGINEERING</h3>
  <p class="abs about-text">Lorem Ipsum is simply dummy text of the printing and typesetting industry. Lorem Ipsum has been the industry's standard dummy text ever since the 1500s, when an remaining essentially unchanged.</p>
  <h4 class="abs mission">Mission Statement</h4>
  <div class="abs mission-items">
    <span><svg class="arrow-bullet" viewBox="0 0 18 18"><path d="M2 2l14 7-14 7 4-7z" fill="none" stroke="#111" stroke-width="1.6" stroke-linejoin="round"/></svg>Company's mission</span>
    <span><svg class="arrow-bullet" viewBox="0 0 18 18"><path d="M2 2l14 7-14 7 4-7z" fill="none" stroke="#111" stroke-width="1.6" stroke-linejoin="round"/></svg>Values</span>
  </div>
  <div class="btn about-btn">Read More</div>
  <div class="abs about-frame"></div>
  <div class="photo about-photo" role="img" aria-label="Tower crane above a concrete building under construction, blue sky"></div>

  <!-- team -->
  <h2 class="abs section-title team-title">OUR TEAM</h2>
  <div class="abs nav-arrow prev" style="left:61px;top:3105px"><svg width="12" height="18" viewBox="0 0 12 18"><path d="M10 2L3 9l7 7" stroke="#333" stroke-width="2" fill="none"/></svg></div>
  <div class="abs nav-arrow next" style="left:1079px;top:3105px"><svg width="12" height="18" viewBox="0 0 12 18"><path d="M2 2l7 7-7 7" stroke="#fff" stroke-width="2" fill="none"/></svg></div>
  <div class="abs team-card" style="left:140px"><div class="team-photo" role="img" aria-label="Portrait of a team member in a blazer and scarf"></div><h4>Lorem ipsum dolor</h4><p>Lorem ipsum dolor sit amet,</p></div>
  <div class="abs team-card" style="left:372px"><div class="team-photo" role="img" aria-label="Portrait of a team member in a black top"></div><h4>Lorem ipsum dolor</h4><p>Lorem ipsum dolor sit amet,</p></div>
  <div class="abs team-card" style="left:604px"><div class="team-photo" role="img" aria-label="Portrait of a team member in a grey cardigan"></div><h4>Lorem ipsum dolor</h4><p>Lorem ipsum dolor sit amet,</p></div>
  <div class="abs team-card" style="left:836px"><div class="team-photo" role="img" aria-label="Portrait of a team member in a white t-shirt"></div><h4>Lorem ipsum dolor</h4><p>Lorem ipsum dolor sit amet,</p></div>

  <!-- testimonials -->
  <h2 class="abs section-title testi-title">CLIENT TESTIMONIALS</h2>
  <div class="abs nav-arrow prev" style="left:61px;top:3604px"><svg width="12" height="18" viewBox="0 0 12 18"><path d="M10 2L3 9l7 7" stroke="#333" stroke-width="2" fill="none"/></svg></div>
  <div class="abs nav-arrow next" style="left:1079px;top:3604px"><svg width="12" height="18" viewBox="0 0 12 18"><path d="M2 2l7 7-7 7" stroke="#fff" stroke-width="2" fill="none"/></svg></div>
  <div class="abs testi-card soft">
    <div class="quote-badge" style="left:64px"><svg width="30" height="24" viewBox="0 0 30 24" fill="#fff"><path d="M0 24V13C0 5 4 1 12 0v5c-4 1-6 3-6 7h6v12zM17 24V13c0-8 4-12 12-13v5c-4 1-6 3-6 7h6v12z"/></svg></div>
    <p class="quote">Lorem ipsum dolor sit amet, consectetur adipisc-ing elit, sed do eiusmod tempor incididunt ut labore et dolore magna aliqua. Quis ipsum sus-</p>
    <div class="testi-avatar" role="img" aria-label="Client portrait"></div>
    <h4>Rowan Teller</h4>
    <p class="role">Lorem Ipsum is simply</p>
  </div>
  <div class="abs testi-card plain">
    <div class="quote-badge" style="left:64px"><svg width="30" height="24" viewBox="0 0 30 24" fill="#fff"><path d="M0 24V13C0 5 4 1 12 0v5c-4 1-6 3-6 7h6v12zM17 24V13c0-8 4-12 12-13v5c-4 1-6 3-6 7h6v12z"/></svg></div>
    <p class="quote">Lorem ipsum dolor sit amet, consectetur adipisc-ing elit, sed do eiusmod tempor incididunt ut labore et dolore magna aliqua. Quis ipsum sus-</p>
    <div class="testi-avatar" role="img" aria-label="Client portrait"></div>
    <h4>Marisol Event</h4>
    <p class="role">Lorem Ipsum is simply</p>
  </div>

  <!-- call to action -->
  <div class="photo cta-bg" role="img" aria-label="Faded city buildings backdrop in pale blue"></div>
  <h2 class="abs section-title cta-title">TOVANDEX4 ARCHITECTURAL ENGINEERING CONSTRUCTION</h2>
  <p class="abs cta-sub">Lorem Ipsum is simply dummy text of the printing and typesetting industry.</p>
  <div class="btn cta-btn">Request A Quote</div>

  <!-- footer -->
  <svg class="abs footer-bg" viewBox="0 0 1200 456" preserveAspectRatio="none">
    <polygon points="0,42 0,456 1200,456 1200,0 880,0" fill="var(--navy)"/>
    <polygon points="0,30 880,-10 1200,60 1200,82 880,18 0,60" fill="var(--blue)"/>
    <polygon points="0,58 880,18 1200,82 1200,90 880,26 0,66" fill="var(--blue-soft)" opacity=".5"/>
  </svg>
  <div class="abs footer-col quick-links">
    <h3>Quick Links</h3>
    <ul><li>Home</li><li>About Us</li><li>Services</li><li>Why Choose Us</li><li>Contact</li></ul>
  </div>
  <div class="abs footer-col contact-info">
    <h3>Contact Info</h3>
    <div class="contact-row" style="margin-top:22px"><svg width="16" height="20" viewBox="0 0 16 20"><path d="M8 0a8 8 0 00-8 8c0 6 8 12 8 12s8-6 8-12a8 8 0 00-8-8z" fill="#fff"/><circle cx="8" cy="8" r="3" fill="var(--navy)"/></svg><span>Lorem ipsum is simply dummy text of the printing and typesetting industry</span></div>
    <div class="contact-row"><svg width="16" height="16" viewBox="0 0 16 16"><path d="M3 0l3 4-2 2c1 2 4 5 6 6l2-2 4 3-2 3C7 16 0 9 0 3z" fill="#fff"/></svg><span>(123) 456-789</span></div>
    <div class="contact-row"><svg width="17" height="13" viewBox="0 0 17 13"><rect x="0.5" y="0.5" width="16" height="12" fill="none" stroke="#fff"/><path d="M1 1l7.5 6L16 1" stroke="#fff" fill="none"/></svg><span>info@tovandex4architectural.com</span></div>
  </div>
  <div class="abs footer-brand">
    <div class="name"><span class="brand-dot"></span>Tovandex4</div>
    <p class="tag">Architectural Engineering Construction</p>
    <div class="socials"><span></span><span></span></div>
  </div>
  <div class="abs copyright">© 2024 Copyright Tovandex4 Architectural Engineering Construction. All Rights</div>

</div>
</body>
</html>
```